KRWB new business card design

We need a business card design for our established business which is Australia wide however based in Melbourne. We are a young team of Financial Planners who specialize in Insurance and Basic super advice for people like us.

We are people who help our clients get things done in a timely and cost effective manner whilst having a good time and a laugh along the way.

We would like this to have a consistent feel with our new e-brochure which i have attached from a color and font perspective.

Industry/Entity Type

Business

Requirements
Must have
• We do not need specific address details rather just the states we are in:

VIC/NSW/QLD/TAS
Nice to have
• Curved edge to mate the brochure

```html
<!DOCTYPE html>
<html lang="en">
<head>
<meta charset="utf-8">
<title>KRWB business card concepts</title>
<link rel="stylesheet" href="https://fonts.googleapis.com/css2?family=Questrial&family=Arimo:ital,wght@0,400;0,700;1,700&display=swap">
<style>
  :root {
    --backdrop: #e6e4e0;
    --card: #0a0a0a;
    --lime: #8dc63f;
    --green: #2fae4a;
    --white: #ffffff;
    --soft-white: #e9e9e9;
  }
  * { box-sizing: border-box; margin: 0; padding: 0; }
  html, body { width: 1200px; height: 502px; overflow: hidden; }
  body {
    position: relative;
    background: var(--backdrop);
    font-family: "Questrial", "Century Gothic", sans-serif;
    color: var(--white);
  }
  .card {
    position: absolute;
    width: 354px;
    height: 204px;
    background: var(--card);
    overflow: hidden;
  }
  .card--contact { left: 35px; top: 30px; border-bottom-right-radius: 28px; }
  .card--portrait { left: 425px; top: 28px; height: 201px; }
  .card--columns { left: 815px; top: 31px; border-bottom-right-radius: 28px; }
  .card--mono { left: 37px; top: 273px; border-top-right-radius: 28px; border-bottom-left-radius: 28px; }
  .card--split { left: 432px; top: 273px; height: 202px; border-bottom-right-radius: 28px; }
  .card--list { left: 817px; top: 278px; border-top-left-radius: 28px; }

  .abs { position: absolute; }
  .wordmark {
    position: absolute;
    display: flex;
    align-items: center;
    gap: 8px;
    color: var(--lime);
    font-family: "Questrial", sans-serif;
    letter-spacing: 1px;
    transform: translate(-50%, -50%);
    white-space: nowrap;
  }
  .wordmark .mark { background: var(--green); flex: none; }
  .wordmark--white { color: var(--white); }
  .wordmark--white .mark { background: var(--white); }

  .heading {
    position: absolute;
    font-weight: 400;
    letter-spacing: 2.5px;
    font-size: 13px;
    color: var(--white);
    white-space: nowrap;
  }
  .centered { left: 0; right: 0; text-align: center; }
  .services { position: absolute; font-size: 12.5px; color: var(--soft-white); white-space: nowrap; }
  .services li { list-style: none; }
  .services li::before { content: "•"; margin-right: 5px; color: var(--lime); }
  .services--mono li::before { color: var(--white); }

  /* contact card */
  .name-plate {
    position: absolute; left: 85px; top: 9px; width: 210px; height: 40px;
    border-radius: 6px;
    background: linear-gradient(#a5d86a, var(--lime) 50%, #6aa82d);
    border: 1px solid #c9e8a4;
    text-align: center;
    font-family: "Arimo", Arial, sans-serif;
    line-height: 1.15;
    padding-top: 4px;
  }
  .name-plate .name { font-weight: 700; font-size: 14px; }
  .name-plate .post { font-style: italic; font-weight: 700; font-size: 9px; }
  .name-plate .role { font-size: 12px; }
  .licence {
    position: absolute; left: 0; right: 0; top: 64px;
    text-align: center; font-family: "Arimo", Arial, sans-serif;
    font-size: 7.5px; line-height: 1.2; color: var(--soft-white);
  }
  .contact-list {
    position: absolute; left: 209px; top: 106px;
    font-family: "Arimo", Arial, sans-serif; font-size: 9px; line-height: 14px;
    list-style: none; color: var(--soft-white);
  }
  .contact-list li { display: flex; align-items: center; gap: 4px; }
  .contact-list svg { width: 8px; height: 8px; fill: var(--soft-white); }
  .states { position: absolute; left: 209px; top: 180px; font-family: "Arimo", Arial, sans-serif; font-size: 10px; }

  .photo-slot {
    position: absolute; right: 0; top: 0; width: 68px; height: 201px;
    background: linear-gradient(180deg, #5a5a5a, #2b2b2b);
    clip-path: path("M20 0 H68 V201 H0 C14 150 20 80 20 0 Z");
  }

  .col-rule { position: absolute; width: 1px; height: 26px; background: var(--green); }
  .services--tight { font-size: 11px; line-height: 15px; }
</style>
</head>
<body>

<!-- Card 1: contact side -->
<section class="card card--contact">
  <div class="name-plate">
    <div class="name">Daniel Harcourt <span class="post">ADFS, BBus, LRS</span></div>
    <div class="role">Financial Adviser</div>
  </div>
  <p class="licence">KRWB Pty Ltd<br>Authorised Representatives, Meridale Financial Planning Limited<br>Australian Financial Services Licensee</p>
  <div class="wordmark" style="left:82px; top:148px; font-size:24px; transform:translate(-50%,-50%);">
    <span class="mark" style="width:12px;height:12px;"></span>KRWB
  </div>
  <svg class="abs" style="left:0;top:0" width="354" height="206" viewBox="0 0 354 206">
    <path d="M190 100 V168 C190 188 178 200 160 206" fill="none" stroke="var(--lime)" stroke-width="3"/>
  </svg>
  <ul class="contact-list">
    <li><svg viewBox="0 0 10 10"><path d="M2 0h2l1 3-1.5 1a6 6 0 0 0 2.5 2.5L7 5l3 1v2c0 1-1 2-2 2A8 8 0 0 1 0 2c0-1 1-2 2-2z"/></svg>1300 555 014</li>
    <li><svg viewBox="0 0 10 10"><rect x="2.5" y="0" width="5" height="10" rx="1"/></svg>0400 555 218</li>
    <li><svg viewBox="0 0 10 10"><rect x="0" y="3" width="10" height="6" rx="1"/><rect x="2" y="0" width="6" height="3"/></svg>03 5550 0192</li>
    <li><svg viewBox="0 0 10 10"><path d="M0 2h10v7H0z M0 2l5 4 5-4" /></svg>daniel@krwb.com.au</li>
    <li><svg viewBox="0 0 10 10"><circle cx="5" cy="5" r="5"/></svg>www.krwb.com.au</li>
  </ul>
  <p class="states">States:&nbsp; VIC/NSW/QLD/TAS</p>
</section>

<!-- Card 2: logo with portrait -->
<section class="card card--portrait">
  <div class="photo-slot" role="img" aria-label="Portrait photo of a smiling team member"></div>
  <svg class="abs" style="left:0;top:0" width="354" height="201" viewBox="0 0 354 201">
    <path d="M292 0 C292 90 286 160 268 201" fill="none" stroke="var(--lime)" stroke-width="3"/>
  </svg>
  <div class="wordmark" style="left:142px; top:60px; font-size:40px;">
    <span class="mark" style="width:18px;height:18px;"></span>KRWB
  </div>
  <h2 class="heading" style="left:0; width:290px; text-align:center; top:121px;">Specialising in:</h2>
  <div class="services" style="left:0; width:290px; top:141px; text-align:center; line-height:18px;">
    <ul>
      <li style="display:inline">Risk Insurance</li> <li style="display:inline">Debt Management</li><br>
      <li style="display:inline">Superannuation</li><br>
      <li style="display:inline">Wealth Creation</li> <li style="display:inline">Retirement Planning</li>
    </ul>
  </div>
</section>

<!-- Card 3: logo with columns -->
<section class="card card--columns">
  <div class="wordmark" style="left:177px; top:68px; font-size:44px;">
    <span class="mark" style="width:20px;height:20px;"></span>KRWB
  </div>
  <h2 class="heading centered" style="top:140px;">Specialising in:</h2>
  <ul class="services services--tight" style="left:16px; top:166px;"><li>Risk Insurance</li><li>Debt Management</li></ul>
  <span class="col-rule" style="left:120px; top:166px;"></span>
  <ul class="services services--tight" style="left:126px; top:166px;"><li>Superannuation</li><li>Wealth Creation</li></ul>
  <span class="col-rule" style="left:222px; top:166px;"></span>
  <ul class="services services--tight" style="left:228px; top:181px;"><li>Retirement Planning</li></ul>
</section>

<!-- Card 4: white logo, centred -->
<section class="card card--mono">
  <div class="wordmark wordmark--white" style="left:177px; top:62px; font-size:44px;">
    <span class="mark" style="width:20px;height:20px;"></span>KRWB
  </div>
  <h2 class="heading centered" style="top:131px;">Specialising in:</h2>
  <div class="services services--mono centered" style="top:150px; line-height:18px;">
    <ul>
      <li style="display:inline">Risk Insurance</li> <li style="display:inline">Debt Management</li> <li style="display:inline">Superannuation</li><br>
      <li style="display:inline">Wealth Creation</li> <li style="display:inline">Retirement Planning</li>
    </ul>
  </div>
  <p class="heading centered" style="top:188px; font-size:11.5px; letter-spacing:3px;">www.krwb.com.au</p>
</section>

<!-- Card 5: split layout -->
<section class="card card--split">
  <div class="wordmark" style="left:88px; top:100px; font-size:32px;">
    <span class="mark" style="width:14px;height:14px;"></span>KRWB
  </div>
  <span class="abs" style="left:174px; top:46px; width:1px; height:118px; background:linear-gradient(transparent, #fff, transparent);"></span>
  <h2 class="heading" style="left:191px; top:45px;">Specialising in:</h2>
  <ul class="services" style="left:191px; top:72px; line-height:21px;">
    <li>Risk Insurance</li><li>Debt Management</li><li>Superannuation</li><li>Wealth Creation</li><li>Retirement Planning</li>
  </ul>
  <svg class="abs" style="left:0;top:0" width="354" height="202" viewBox="0 0 354 202">
    <path d="M349 0 H354 V174 C354 190 342 202 326 202 H300 C322 202 349 196 349 170 Z" fill="var(--lime)"/>
  </svg>
</section>

<!-- Card 6: list with logo on right -->
<section class="card card--list">
  <h2 class="heading" style="left:27px; top:26px; font-size:16px; letter-spacing:3px;">Specialising in:</h2>
  <ul class="services" style="left:27px; top:52px; font-size:15.5px; line-height:25px;">
    <li>Risk Insurance</li><li>Debt Management</li><li>Superannuation</li><li>Wealth Creation</li><li>Retirement Planning</li>
  </ul>
  <div class="wordmark" style="left:272px; top:104px; font-size:30px;">
    <span class="mark" style="width:13px;height:13px;"></span>KRWB
  </div>
</section>

</body>
</html>
```